Building company buisness cards

We are looking for a sharp modern new look for our business cards.
We are a New Zealand based company that specialises in house and land packages.
We have attached a photo of the current logo and would like to see if it can be improved somehow if needed.
We are open to any colours but we have chosen green at this stage.
Feel free to change the font and make the logo smarter looking.
Play with the colours and see what looks best.

We want a card that looks so good know one will want to throw it away!

Target Market(s)

Home buyers

Industry/Entity Type

Building

Contact Information for Business Card

Derek Tolvane
0217394062
dtolvane@quillmarkhomesteads.co.nz
quillmarkhomesteads.co.nz

Font styles to use
Serif
Sans Serif

Colors

Designer to choose colors to be used in the design.

Requirements
Must have
• Logo and company name on one side, details on the other side
Nice to have
• Color codes for the original green are HEX #4a8028, RGB(74,128,40), CMYK(42,0,69,50)
• Round corners, Raised and/or spot UV

```html
<!DOCTYPE html>
<html lang="en">
<head>
<meta charset="utf-8">
<title>Quillmark Homesteads — Business Cards</title>
<link href="https://fonts.googleapis.com/css2?family=Lato:wght@400;700&display=swap" rel="stylesheet">
<style>
  :root {
    --backdrop: #5a5a5a;
    --card-light: #f3f3f3;
    --brand-green: #4a8028;
    --ink: #2b2b2b;
    --white: #ffffff;
  }
  * { margin: 0; padding: 0; box-sizing: border-box; }
  html, body {
    width: 1200px; height: 900px; overflow: hidden;
    background: var(--backdrop);
  }
  .canvas { position: relative; width: 1200px; height: 900px; }

  .card {
    position: absolute; top: 200px; width: 310px; height: 502px;
  }
  .card--details {
    left: 253px; background: var(--card-light);
    border-radius: 62px 0 62px 0;
  }
  .card--brand {
    left: 627px; background: var(--brand-green);
    border-radius: 0 62px 0 62px;
  }

  .company-name {
    position: absolute; left: 0; right: 0; text-align: center;
    font-family: "Lato", sans-serif; font-weight: 700;
    font-size: 24px; line-height: 1;
  }
  .card--details .company-name { top: 158px; color: var(--brand-green); }
  .card--brand .company-name { top: 246px; color: var(--white); }

  .contact {
    position: absolute; left: 19px; top: 380px;
    font-family: "Lato", sans-serif; color: var(--ink);
  }
  .contact__name {
    font-weight: 700; font-size: 17px; color: var(--brand-green);
    text-transform: uppercase; letter-spacing: 0.2px; margin-bottom: 12px;
  }
  .contact__list { list-style: none; }
  .contact__item {
    display: flex; align-items: center; gap: 6px;
    font-size: 14px; line-height: 17px;
  }
  .contact__icon { width: 11px; height: 11px; flex: none; fill: var(--brand-green); }
</style>
</head>
<body>
<main class="canvas">

  <section class="card card--details">
    <p class="company-name">Quillmark Homesteads</p>

    <div class="contact">
      <p class="contact__name">Derek Tolvane</p>
      <ul class="contact__list">
        <li class="contact__item">
          <svg class="contact__icon" viewBox="0 0 12 12" aria-hidden="true"><path d="M1 4c0-2 2-3 5-3s5 1 5 3v1H8.5V3.6C7.7 3.3 4.3 3.3 3.5 3.6V5H1z"/><path d="M3 6h6l1.5 5h-9z"/></svg>
          <span>0217394062</span>
        </li>
        <li class="contact__item">
          <svg class="contact__icon" viewBox="0 0 12 12" aria-hidden="true"><path d="M0.5 2.5h11v7h-11z"/><path d="M1.5 3.3l4.5 3.4 4.5-3.4" fill="none" stroke="var(--card-light)" stroke-width="0.9"/></svg>
          <span>dtolvane@quillmarkhomesteads.co.nz</span>
        </li>
        <li class="contact__item">
          <svg class="contact__icon" viewBox="0 0 12 12" aria-hidden="true"><circle cx="6" cy="6" r="5.5"/><path d="M0.8 6h10.4M6 0.6c-2.6 3-2.6 7.8 0 10.8M6 0.6c2.6 3 2.6 7.8 0 10.8" fill="none" stroke="var(--card-light)" stroke-width="0.8"/></svg>
          <span>www.quillmarkhomesteads.co.nz</span>
        </li>
      </ul>
    </div>
  </section>

  <section class="card card--brand">
    <p class="company-name">Quillmark Homesteads</p>
  </section>

</main>
</body>
</html>
```